Slow Winter Song. A CD of beautiful 17th century music for lute played by a world famous lutenist.

Hi designers,
My name is Ollie Pellicott and I am an international lute player in need of a CD cover design. I am blind, so will be relying on other people's eyes and descriptions during the process, including yours! Are you up for the challenge?
My CD is called Slow Winter Song. It's beautiful lute music from the 17th century, very intimate and carming, but also very powerful.
I would like you to use the attached image, and find a way to include the following text in a tasteful way:
The text for the front cover is as follows:
Slow Winter Song
Oliver Pellicott - lute and theorbo
Music by Harcrane, Fennimore, Brackley, Tarn, Cavallenti and Ruhlendorf.
Here is a viewora link to some of the music I play, which should give you an idea:
www.viewora.net/olliepellicott1
Here is a link to my website, where you can see the covers of my other CDs, and get more information about me:
www.oliverpellicott.net
I'm excited to receive your design and ideas.
Best wishes
Ollie

```html
<!DOCTYPE html>
<html lang="en">
<head>
<meta charset="utf-8">
<title>Slow Winter Song – Oliver Pellicott</title>
<link rel="stylesheet" href="https://fonts.googleapis.com/css2?family=Playfair+Display:wght@700;900&family=Michroma&display=swap">
<style>
  :root {
    --page-bg: #e9e9e9;
    --photo-dark: #1c140c;
    --photo-mid: #4a3520;
    --wood-glow: #d9a25a;
    --room-light: #b9b2a4;
    --panel-light: rgba(235, 232, 226, 0.72);
    --panel-fade: rgba(200, 196, 188, 0.35);
    --credit-panel: rgba(150, 146, 140, 0.72);
    --title-ink: #0b0b0b;
    --credit-ink: #121212;
  }
  * { margin: 0; padding: 0; box-sizing: border-box; }
  html, body {
    width: 1200px; height: 1200px; overflow: hidden;
    background: var(--page-bg);
  }
  .cover {
    position: absolute; left: 60px; top: 60px;
    width: 1080px; height: 1080px; overflow: hidden;
    box-shadow: 0 10px 30px rgba(0,0,0,0.25);
  }
  .cover-photo {
    position: absolute; inset: 0;
    background:
      radial-gradient(ellipse 220px 380px at 300px 700px, var(--wood-glow) 0%, rgba(217,162,90,0.55) 45%, transparent 100%),
      radial-gradient(ellipse 260px 180px at 330px 140px, rgba(120,90,40,0.6) 0%, transparent 100%),
      linear-gradient(90deg, var(--photo-dark) 0%, var(--photo-mid) 45%, var(--room-light) 85%, #8a8276 100%);
  }
  .title-panel {
    position: absolute; left: 573px; top: 0;
    width: 507px; height: 756px;
    background: linear-gradient(180deg, var(--panel-light) 0%, rgba(225,222,215,0.6) 70%, var(--panel-fade) 100%);
    display: flex; flex-direction: column; align-items: center; justify-content: center;
    padding-top: 20px;
  }
  .album-title {
    font-family: "Playfair Display", serif;
    font-weight: 900;
    color: var(--title-ink);
    font-size: 200px;
    line-height: 0.98;
    text-align: center;
    transform: scaleX(0.6);
    text-shadow: 4px 6px 8px rgba(0,0,0,0.35);
    letter-spacing: -2px;
  }
  .album-title span { display: block; }
  .credit-panel {
    position: absolute; left: 573px; top: 790px;
    width: 507px; height: 252px;
    background: var(--credit-panel);
    font-family: "Michroma", sans-serif;
    color: var(--credit-ink);
    text-align: center;
    text-transform: uppercase;
  }
  .performer {
    margin-top: 40px;
    font-size: 22px; line-height: 1.5; letter-spacing: 2px;
  }
  .composers {
    margin-top: 34px;
    font-size: 17px; line-height: 1.45; letter-spacing: 1px;
  }
</style>
</head>
<body>
  <div class="cover">
    <div class="cover-photo" role="img" aria-label="Photograph of a lute leaning in a dim, candlelit period room with a chandelier"></div>
    <div class="title-panel">
      <h1 class="album-title"><span>Slow</span><span>Winter</span><span>Song</span></h1>
    </div>
    <div class="credit-panel">
      <p class="performer">Oliver Pellicott<br>Lute and Theorbo</p>
      <p class="composers">Music by:<br>Harcrane • Fennimore • Brackley<br>Tarn • Cavallenti • Ruhlendorf</p>
    </div>
  </div>
</body>
</html>
```